Meridian Crestline Motors *

Professional business cards for our auto wholesale dealership.

Target Market(s)

New and used cars sales managers and middle class to higher end private party buyers.

Industry/Entity Type

Automotive

Contact Information for Business Card

Meridian Crestline Motors
Darnell R Okonski
Owner
(555) 304-6618
mercrestmotors@quillbox.example
Dealer Lic # 48265

Logo Text

Meridian Crestline Motors, Mer Crest Motors, MCM, etc

Font styles to use
Serif
Sans Serif

Colors

Designer to choose colors to be used in the design.

Requirements
Must have
• A professional, but not pretentious, look
Nice to have
• It might be nice to see "MCM" in a shape form i.e. circle, triangle, etc in the corner or background somehwere
Should not have
• bright "girly" colors

```html
<!DOCTYPE html>
<html lang="en">
<head>
<meta charset="utf-8">
<title>Meridian Crestline Motors — Business Cards</title>
<link rel="stylesheet" href="https://fonts.googleapis.com/css2?family=Open+Sans:wght@400;600;800&display=swap">
<style>
  :root {
    --stage: #3b3b3d;
    --card: #1c1c1d;
    --card-edge: #262628;
    --red: #e31b23;
    --gold: #e3b50f;
    --white: #ffffff;
    --muted: #d9d9d9;
    --ink: #111111;
  }
  * { box-sizing: border-box; margin: 0; padding: 0; }
  html, body { width: 1200px; height: 1200px; overflow: hidden; }
  body {
    background: var(--stage);
    font-family: "Open Sans", Arial, sans-serif;
    display: flex;
    flex-direction: column;
    align-items: center;
    justify-content: center;
    gap: 60px;
  }
  .card {
    position: relative;
    width: 840px;
    height: 480px;
    border-radius: 18px;
    background: linear-gradient(160deg, var(--card-edge), var(--card) 60%);
    overflow: hidden;
    box-shadow: 0 14px 34px rgba(0,0,0,.45);
  }
  .card__band {
    position: absolute; left: 0; right: 0; bottom: 0;
    height: 40px; background: var(--red);
  }
  .card__rule {
    position: absolute; left: 0; right: 0;
    height: 3px; background: var(--gold);
  }
  .emblem {
    position: absolute;
    border-radius: 50%;
    background: var(--red);
    display: flex; align-items: center; justify-content: center;
    color: var(--ink);
    font-weight: 800;
    letter-spacing: 1px;
  }

  /* Front */
  .card--front .card__rule { bottom: 54px; }
  .card--front .emblem {
    left: 70px; top: 70px; width: 190px; height: 190px;
    font-size: 56px;
  }
  .brand {
    color: var(--white);
    line-height: 1;
  }
  .brand__name { font-weight: 800; text-transform: uppercase; display: block; }
  .brand__sub { font-weight: 600; display: block; }
  .card--front .brand { position: absolute; left: 290px; top: 205px; }
  .card--front .brand__name { font-size: 46px; letter-spacing: .5px; }
  .card--front .brand__sub { font-size: 38px; margin-top: 8px; }

  /* Back */
  .card--back .card__rule { top: 228px; }
  .card--back .brand { position: absolute; left: 60px; top: 50px; }
  .card--back .brand__name { font-size: 30px; }
  .card--back .brand__sub { font-size: 22px; margin-top: 4px; }
  .holder {
    position: absolute; left: 60px; top: 140px;
    display: flex; gap: 14px; align-items: flex-start;
  }
  .holder__mark {
    width: 12px; height: 44px; border-radius: 6px; background: var(--gold);
    margin-top: 4px;
  }
  .holder__name { color: var(--white); font-size: 24px; font-weight: 600; line-height: 1.1; }
  .holder__role { color: var(--muted); font-size: 17px; }
  .contact {
    position: absolute; left: 60px; top: 258px;
    list-style: none;
    color: var(--muted);
    font-size: 17px;
  }
  .contact li { display: flex; align-items: center; gap: 12px; height: 34px; }
  .contact svg { width: 18px; height: 18px; flex: none; }
  .contact .contact__plain { padding-left: 0; }
  .card--back .emblem {
    left: 540px; top: 114px; width: 230px; height: 230px;
    font-size: 66px;
  }
</style>
</head>
<body>

  <section class="card card--front" aria-label="Business card front">
    <div class="emblem">MCM</div>
    <div class="brand">
      <span class="brand__name">Meridian Crestline</span>
      <span class="brand__sub">Motors</span>
    </div>
    <div class="card__rule"></div>
    <div class="card__band"></div>
  </section>

  <section class="card card--back" aria-label="Business card back">
    <div class="brand">
      <span class="brand__name">Meridian Crestline</span>
      <span class="brand__sub">Motors</span>
    </div>
    <div class="holder">
      <div class="holder__mark"></div>
      <div>
        <div class="holder__name">Darnell R Okonski</div>
        <div class="holder__role">Owner</div>
      </div>
    </div>
    <div class="card__rule"></div>
    <div class="emblem">MCM</div>
    <ul class="contact">
      <li>
        <svg viewBox="0 0 24 24" aria-hidden="true"><path fill="none" stroke="#e3b50f" stroke-width="2.2" stroke-linecap="round" d="M6 3l3 4-2 2c1 3 4 6 7 7l2-2 4 3-2 3C11 20 4 13 3 5z"/></svg>
        (555) 304-6618
      </li>
      <li>
        <svg viewBox="0 0 24 24" aria-hidden="true"><rect x="2.5" y="5" width="19" height="14" fill="none" stroke="#e3b50f" stroke-width="2"/><path d="M3 6l9 7 9-7" fill="none" stroke="#e3b50f" stroke-width="2"/></svg>
        mercrestmotors@quillbox.example
      </li>
      <li class="contact__plain">Dealer Lic # 48265</li>
    </ul>
    <div class="card__band"></div>
  </section>

</body>
</html>
```